Promotional Postcard for Mountain Bike Stunt Show

PLEASE DOWNLOAD ATTACHED ZIP FILE

This will be on a larger postcard size: 4ā€ x 9ā€ - front and back will be completely covered in text and pictures. I’m going to mail it out in envelopes.

Overview: This is promotional postcard for my mountain bike stunt show. It will be filled with text and pictures to attract clients into booking my show. It must look clean and professional. Remember: This is an action stunt show based out of the mountain states region so it must look exciting, rugged, clean and professional :)

A few additional notes: I'd also like to see the logo picture 1 used on the front to display the name of my show but then fade out to the right into whatever else you want to fit. As far as all of the text, try to put that in "dead space" in the pictures if there open air or in Picture 3 where theres an opportunity to fade out the unwanted trailer and grass showing and put text in there "action packed etc etc"

Target Market(s)

Trade shows, fairs, schools, festivals, agricultural fairs, corporate events

Industry/Entity Type

Entertainment Industry

Colors

Designer to choose colors to be used in the design.

Requirements
Must have
• FOLLOW INSTRUCTIONS IN MY ATTACHED ZIP FILE
Nice to have
• I think I'd like a dark theme/layout to the card :)

```html
<!DOCTYPE html>
<html lang="en">
<head>
<meta charset="utf-8">
<title>Danny Kessler's Mountain Bike Trials Stunt Show – Postcard</title>
<link rel="stylesheet" href="https://fonts.googleapis.com/css2?family=Russo+One&family=Patrick+Hand+SC&family=Rubik+Dirt&family=Open+Sans:wght@400;600;700&family=Encode+Sans+Condensed:wght@300&family=Yellowtail&display=swap">
<style>
  :root {
    --page-bg: #6097cc;
    --card-bg: #eeeeee;
    --card-white: #ffffff;
    --navy: #253f5c;
    --blue: #2d8fd0;
    --blue-light: #5fb3e6;
    --blue-label: #3e96d3;
    --red: #b01c24;
    --red-dark: #8d1219;
    --ink: #222222;
    --body-text: #444444;
  }
  * { box-sizing: border-box; margin: 0; padding: 0; }
  html, body { width: 1200px; height: 791px; overflow: hidden; }
  body { background: var(--page-bg); position: relative; font-family: "Open Sans", sans-serif; }

  .card {
    position: absolute; left: 80px; width: 1040px; height: 365px;
    overflow: hidden; box-shadow: 0 4px 10px rgba(0,0,0,.25);
  }
  .card--front { top: 22px; background: radial-gradient(ellipse at 55% 45%, #f7f7f7, var(--card-bg) 70%, #dcdcdc); }
  .card--back { top: 405px; background: var(--card-white); }
  .card__strip { position: absolute; left: 0; right: 0; bottom: 0; height: 9px; background: var(--blue); }

  /* Front */
  .front__swirl { position: absolute; left: 0; top: 0; width: 420px; height: 365px; }
  .front__headline {
    position: absolute; left: 300px; width: 480px; top: 16px; text-align: center; white-space: nowrap;
    font-family: "Russo One", sans-serif; color: var(--navy); font-size: 29px; line-height: 40px;
    letter-spacing: .5px;
  }
  .front__tagline {
    position: absolute; left: 392px; top: 108px; width: 290px; height: 32px;
    background: var(--blue-label); color: #fff; transform: rotate(-1deg);
    font-family: "Patrick Hand SC", cursive; font-size: 22px; line-height: 32px; text-align: center;
    box-shadow: 0 2px 4px rgba(0,0,0,.25); white-space: nowrap;
  }
  .front__stamp {
    position: absolute; left: 420px; top: 168px; width: 320px; text-align: center;
    transform: rotate(-14deg); transform-origin: center;
    font-family: "Rubik Dirt", sans-serif; color: #fff; font-size: 46px; line-height: 50px;
    -webkit-text-stroke: 6px var(--red); paint-order: stroke fill;
    text-shadow: 3px 3px 0 var(--red-dark);
  }
  .front__hexes { position: absolute; left: 720px; top: 0; width: 320px; height: 365px; }
  .feature-label {
    position: absolute; color: #fff; font-weight: 700; font-size: 11px; line-height: 12px;
    text-align: center; padding: 4px 6px; box-shadow: 0 2px 3px rgba(0,0,0,.25); white-space: nowrap;
  }
  .feature-label--blue { background: var(--blue-label); }
  .feature-label--red { background: var(--red); font-size: 10.5px; }
  .feature-label--audience { left: 716px; top: 62px; width: 100px; }
  .feature-label--meet { left: 878px; top: 166px; width: 112px; }
  .feature-label--giveaways { left: 728px; top: 262px; width: 100px; }

  /* Back */
  .back__photo {
    position: absolute; left: 0; top: 0; width: 440px; height: 258px;
    background:
      linear-gradient(90deg, rgba(255,255,255,0) 70%, #fff 100%),
      linear-gradient(180deg, #c9ccd0 0%, #9aa0a6 38%, #6f6a6c 60%, #d7d7d9 78%, #e8e8e8 100%);
  }
  .back__copy {
    position: absolute; left: 420px; top: 6px; width: 230px;
    font-family: "Encode Sans Condensed", sans-serif; font-weight: 300; color: var(--body-text);
    font-size: 16.5px; line-height: 27px; text-align: justify; letter-spacing: .2px;
  }
  .back__header {
    position: absolute; left: 654px; top: 0; width: 386px; height: 154px;
    background:
      linear-gradient(180deg, rgba(255,255,255,0) 78%, rgba(255,255,255,.95) 100%),
      linear-gradient(100deg, #7b5a3e 0%, #a77a52 28%, #8fb3d3 55%, #d7e8f4 80%, #ffffff 100%);
  }
  .back__show-name {
    position: absolute; left: 764px; top: 34px; font-family: "Yellowtail", cursive;
    color: #fff; font-size: 24px; line-height: 30px; text-shadow: 1px 1px 2px rgba(0,0,0,.5);
  }
  .back__show-title {
    position: absolute; left: 690px; top: 66px; width: 320px; text-align: center;
    font-family: "Russo One", sans-serif; color: #fff; font-size: 19px; line-height: 22px;
    text-shadow: 1px 1px 2px rgba(0,0,0,.6);
  }
  .back__social { position: absolute; left: 672px; top: 132px; display: flex; align-items: center; gap: 4px; font-size: 11px; font-weight: 600; color: var(--ink); }
  .back__social-mark { width: 10px; height: 10px; background: var(--red); }
  .back__url-small { position: absolute; left: 812px; top: 134px; font-size: 11px; font-weight: 700; color: var(--ink); }

  .booking { position: absolute; left: 667px; top: 156px; }
  .booking__heading { font-weight: 700; color: var(--blue); font-size: 18px; line-height: 26px; }
  .booking__name { font-weight: 700; color: var(--red); font-size: 19px; line-height: 29px; }
  .booking__row { display: flex; align-items: center; gap: 12px; font-weight: 700; color: var(--ink); font-size: 19px; line-height: 28px; white-space: nowrap; }
  .booking__icon { width: 18px; height: 18px; flex: none; }

  .venues__banner {
    position: absolute; left: 20px; top: 252px; width: 414px; height: 30px;
    background: var(--red); color: #fff; font-weight: 700; font-size: 15px; line-height: 30px;
    padding-left: 22px; border-top-right-radius: 22px; border-bottom-right-radius: 4px; white-space: nowrap;
  }
  .venues__row { position: absolute; left: 22px; top: 292px; width: 1000px; height: 50px; display: flex; align-items: center; justify-content: space-between; }
  .venue { flex: none; }
  .venue--round { width: 42px; height: 42px; border-radius: 50%; border: 3px solid #8a1d22; background: #f3e8e0; }
  .venue--round.alt { border-color: #2b2b2b; background: #555; }
  .venue--wide { width: 70px; height: 28px; background: #244e8f; }
  .venue--wide.yellow { width: 42px; height: 36px; background: #f3e21c; }
  .venue--wide.teal { background: #3d6fae; }
  .venue--low { align-self: flex-end; margin-bottom: 6px; }
  .venue--wide.grey { width: 118px; height: 16px; background: #6b7a3a; }
  .venue--wide.light { width: 82px; height: 16px; background: #c3c6cf; }
  .venue--wide.red { width: 96px; height: 16px; background: #b8282e; }
</style>
</head>
<body>

<section class="card card--front" aria-label="Postcard front">
  <svg class="front__swirl" viewBox="0 0 420 365">
    <defs>
      <linearGradient id="swirlDeep" x1="0" y1="0" x2="1" y2="1">
        <stop offset="0" stop-color="#1f7fc4"/><stop offset="1" stop-color="#4cb0ea"/>
      </linearGradient>
      <linearGradient id="swirlPale" x1="0" y1="0" x2="1" y2="1">
        <stop offset="0" stop-color="#bfe2f6"/><stop offset="1" stop-color="#7cc3ec"/>
      </linearGradient>
      <linearGradient id="heroPhoto" x1="0" y1="0" x2="0" y2="1">
        <stop offset="0" stop-color="#4ea7e6"/><stop offset=".45" stop-color="#9bcdf0"/>
        <stop offset=".6" stop-color="#a74a3b"/><stop offset=".75" stop-color="#6a8e3e"/><stop offset="1" stop-color="#4f8a2d"/>
      </linearGradient>
      <radialGradient id="bubble" cx=".35" cy=".35" r=".7">
        <stop offset="0" stop-color="#e4f4ff"/><stop offset=".5" stop-color="#5fb3e6"/><stop offset="1" stop-color="#1f7fc4"/>
      </radialGradient>
    </defs>
    <path d="M150 -40 A235 215 0 0 1 180 365 A208 195 0 0 0 150 -40Z" fill="url(#swirlPale)"/>
    <path d="M120 -20 A205 190 0 0 1 140 355 A172 175 0 0 0 120 -20Z" fill="url(#swirlDeep)"/>
    <circle cx="160" cy="178" r="140" fill="url(#heroPhoto)" stroke="#fff" stroke-width="3" role="img" aria-label="Photo: rider balancing a trials bike in mid-air above a ramp in front of a fairground crowd"/>
    <circle cx="238" cy="14" r="13" fill="url(#bubble)"/>
    <circle cx="360" cy="306" r="20" fill="url(#bubble)"/>
  </svg>

  <h1 class="front__headline">AWESOME ENTERTAINMENT<br>FOR YOUR EVENT!</h1>
  <p class="front__tagline">Loads of high-energy action!</p>
  <p class="front__stamp">THIS<br>SHOW<br>DELIVERS!</p>

  <svg class="front__hexes" viewBox="720 0 320 365">
    <defs>
      <linearGradient id="hexAudience" x1="0" y1="0" x2="0" y2="1">
        <stop offset="0" stop-color="#6cb6ea"/><stop offset=".55" stop-color="#b7d7ee"/><stop offset="1" stop-color="#5d9a37"/>
      </linearGradient>
      <linearGradient id="hexAutograph" x1="0" y1="0" x2="1" y2="1">
        <stop offset="0" stop-color="#e9e5df"/><stop offset=".5" stop-color="#9b8a7d"/><stop offset="1" stop-color="#4d6aa8"/>
      </linearGradient>
      <linearGradient id="hexGiveaway" x1="0" y1="0" x2="1" y2="1">
        <stop offset="0" stop-color="#6f8d4b"/><stop offset=".5" stop-color="#2c2c2e"/><stop offset="1" stop-color="#c9c9cf"/>
      </linearGradient>
    </defs>
    <polygon points="881,19 936,51 936,115 881,147 826,115 826,51" fill="url(#hexAudience)" stroke="#fff" stroke-width="5" role="img" aria-label="Photo: rider high-fiving a young fan on the grass beside the show trailer"/>
    <polygon points="814,118 868,149 868,211 814,242 760,211 760,149" fill="url(#hexAutograph)" stroke="#fff" stroke-width="5" role="img" aria-label="Photo: kids lining up at a table for an autograph session"/>
    <polygon points="902,218 957,250 957,314 902,346 847,314 847,250" fill="url(#hexGiveaway)" stroke="#fff" stroke-width="5" role="img" aria-label="Photo: bagged stickers and giveaway items on a table"/>
  </svg>

  <p class="feature-label feature-label--blue feature-label--audience">AUDIENCE<br>ENGAGEMENT!</p>
  <p class="feature-label feature-label--red feature-label--meet">Meet n' greet<br>autograph session</p>
  <p class="feature-label feature-label--blue feature-label--giveaways">FREE<br>GIVEAWAYS!</p>

  <div class="card__strip"></div>
</section>

<section class="card card--back" aria-label="Postcard back">
  <div class="back__photo" role="img" aria-label="Photo: rider hopping a green trials bike onto a red box at an indoor expo hall while a crowd watches"></div>

  <p class="back__copy">Danny is a pro, showcasing the most technical aspects of mountain biking as he rides over seemingly impossible obstacles with his bike. Danny's charismatic personality, coupled with his 20 years of trials experience, makes for an unforgettable stunt display of balance and skill.</p>

  <div class="back__header" role="img" aria-label="Photo: rider on a trials bike atop red rocks with snowy mountains behind"></div>
  <p class="back__show-name">Danny Kessler's</p>
  <p class="back__show-title">MOUNTAIN BIKE TRIALS<br>STUNT SHOW</p>
  <p class="back__social"><span class="back__social-mark"></span>kesslertrials</p>
  <p class="back__url-small">www.kesslertrials.com</p>

  <div class="booking">
    <p class="booking__heading">Booking Info:</p>
    <p class="booking__name">Danny Kessler</p>
    <p class="booking__row">
      <svg class="booking__icon" viewBox="0 0 20 20" aria-hidden="true"><circle cx="10" cy="10" r="9" fill="none" stroke="#b01c24" stroke-width="1.6"/><path d="M5.5 8.5 Q10 5 14.5 8.5 L13 10 L11.5 9 L8.5 9 L7 10Z M7 10.5 H13 L13.5 14 H6.5Z" fill="#b01c24"/></svg>
      (555) 014-2290
    </p>
    <p class="booking__row">
      <svg class="booking__icon" viewBox="0 0 20 20" aria-hidden="true"><circle cx="10" cy="10" r="9" fill="none" stroke="#b01c24" stroke-width="1.6"/><rect x="5" y="6.5" width="10" height="7" fill="#b01c24"/><path d="M5 6.5 L10 10.5 L15 6.5" fill="none" stroke="#fff" stroke-width="1.2"/></svg>
      danny@kesslertrials.com
    </p>
    <p class="booking__row">
      <svg class="booking__icon" viewBox="0 0 20 20" aria-hidden="true"><circle cx="10" cy="10" r="8" fill="none" stroke="#b01c24" stroke-width="1.6"/><ellipse cx="10" cy="10" rx="3.5" ry="8" fill="none" stroke="#b01c24" stroke-width="1.2"/><path d="M2 10 H18 M3.5 6 H16.5 M3.5 14 H16.5" stroke="#b01c24" stroke-width="1.2"/></svg>
      www.kesslertrials.com
    </p>
  </div>

  <p class="venues__banner">Past venues where Danny has performed:</p>
  <div class="venues__row" aria-label="Past venue badges">
    <span class="venue venue--round"></span>
    <span class="venue venue--round"></span>
    <span class="venue venue--round alt"></span>
    <span class="venue venue--round"></span>
    <span class="venue venue--round"></span>
    <span class="venue venue--wide"></span>
    <span class="venue venue--wide yellow"></span>
    <span class="venue venue--wide teal"></span>
    <span class="venue venue--round" style="border-color:#2d6fae;background:#fff;"></span>
    <span class="venue venue--wide grey venue--low"></span>
    <span class="venue venue--wide light venue--low"></span>
    <span class="venue venue--wide red venue--low"></span>
  </div>

  <div class="card__strip"></div>
</section>

</body>
</html>
```